Corinnehabbard.com

1. Conceptualization and designing of the site Homepage. The Homepage design will be completely customized and based on your design instructions (i.e. preferred colors, links to reference sites that you want us to take reference from if any etc) and the recently completed logo design.
2. Upon homepage design approval, based on it we will be creating the layout for the other 4 site inner pages (i.e. About page, Contact page, Services page, and Insights (publications, media).
3. Once all the inner page designs are approved, we will get the designs built (will make sure that the site is completely Responsive - works on all devices) within your provided WIX account.
4. We will add the static text and images provided by you to the Home page, About page, Contact page, and the Services page. For the 2 Insights sub-pages, we will add 1-2 sample Publications and Media entries.
once you confirm the total number of required entries for the 2 sub-pages, I will accordingly quote you on the same
5. Integration of a Contact form on the Contact page that will email the filled in details to your mail id.

```html
<!DOCTYPE html>
<html lang="en">
<head>
<meta charset="utf-8">
<title>Corinne Habbard Consulting</title>
<link rel="stylesheet" href="https://fonts.googleapis.com/css2?family=Hedvig+Letters+Serif&family=Arimo:wght@400;700&display=swap">
<style>
:root{
  --blue:#2a8fd1;
  --heading-blue:#1a8bc9;
  --orange:#f29611;
  --green:#229140;
  --ink:#111;
  --white:#fff;
  --serif:"Hedvig Letters Serif", Georgia, serif;
  --sans:Arimo, Arial, sans-serif;
}
*{box-sizing:border-box;margin:0;padding:0}
html,body{width:1200px;height:3795px;overflow:hidden;background:var(--white)}
body{position:relative;font-family:var(--sans);color:var(--ink)}
.abs{position:absolute}
.btn{position:absolute;display:flex;align-items:center;justify-content:center;background:var(--blue);color:var(--white);border-radius:24px;font-family:var(--serif);font-size:18px;box-shadow:0 4px 8px rgba(0,0,0,.2)}
/* header */
.site-header{position:absolute;top:0;left:0;width:1200px;height:86px;background:var(--white);z-index:2}
.brand-badge{position:absolute;left:106px;top:0;width:192px;height:112px;background:var(--white);border-radius:0 0 60px 60px;box-shadow:0 2px 8px rgba(0,0,0,.15);display:flex;flex-direction:column;align-items:center;justify-content:flex-start;padding-top:10px}
.brand-dot{width:52px;height:52px;border-radius:50%;background:var(--heading-blue);margin-bottom:8px}
.brand-name{font-family:var(--sans);font-weight:700;font-size:13px;color:var(--heading-blue);text-align:center;line-height:1.15;letter-spacing:.3px;white-space:nowrap}
.brand-name small{display:block;font-size:10px;letter-spacing:3px;font-weight:700}
.nav a{position:absolute;top:30px;font-family:var(--serif);font-size:18px;color:var(--ink);text-decoration:none}
.nav a.active{color:var(--blue);text-decoration:underline}
/* hero */
.hero{position:absolute;top:86px;left:0;width:1200px;height:600px;overflow:hidden}
.hero-photo{position:absolute;inset:0;background:
  radial-gradient(ellipse 200px 260px at 760px 260px,rgba(150,110,80,.55),transparent 70%),
  radial-gradient(ellipse 260px 420px at 1060px 330px,rgba(20,20,28,.9),transparent 75%),
  linear-gradient(90deg,#2e2e2e 0%,#4a4845 30%,#77706a 55%,#8a7f74 72%,#3a3838 100%)}
.hero-photo::after{content:"";position:absolute;left:0;right:0;bottom:0;height:170px;background:linear-gradient(180deg,rgba(200,200,200,0),rgba(190,190,190,.35))}
.hero-welcome{left:110px;top:170px;font-size:21px;color:var(--white)}
.hero-title{left:110px;top:200px;font-family:var(--serif);font-size:46px;line-height:64px;color:var(--white);font-weight:400}
/* about */
.section-title{font-family:var(--serif);font-weight:400;color:var(--heading-blue)}
.about-title{left:105px;top:786px;font-size:34px}
.about-text{left:105px;top:840px;width:455px;font-size:14.5px;line-height:31px;color:var(--ink)}
.about-text p+p{margin-top:31px}
.portrait{position:absolute;left:637px;top:809px;width:422px;height:422px;border-radius:50%;background:
  radial-gradient(ellipse 150px 200px at 50% 55%,#a07d66,#5a3b2a 70%,transparent 72%),
  linear-gradient(180deg,#d4d4d4,#b8b8b8 70%,#222 100%)}
/* insights */
.insights{position:absolute;top:1365px;left:0;width:1200px;height:755px;background:radial-gradient(ellipse at 50% 50%,#f7a730,var(--orange) 70%)}
.insights-title{width:1200px;text-align:center;top:88px;font-size:36px;color:var(--white)}
.book{position:absolute;top:172px;width:245px;height:379px;background:linear-gradient(90deg,#e6e6e6,#fafafa 40%,#e9e9e9 85%,#cfcfcf);box-shadow:6px 10px 20px rgba(0,0,0,.25);display:flex;flex-direction:column;align-items:center;justify-content:center}
.book .brand-dot{width:50px;height:50px;margin-bottom:6px}
.book .brand-name{font-size:14px}
.book-caption{position:absolute;top:590px;width:300px;text-align:center;font-weight:700;font-size:16.5px;line-height:33px;color:var(--white)}
/* services */
.services-title{width:1200px;text-align:center;top:2195px;font-size:34px;color:var(--heading-blue)}
.services-intro{left:170px;top:2255px;width:860px;text-align:center;font-size:14.5px;line-height:31px}
.service-card{position:absolute;top:2345px;width:471px;height:366px;border:1px solid #ddd;border-radius:12px;box-shadow:0 2px 6px rgba(0,0,0,.1);background:var(--white)}
.service-img{position:absolute;left:21px;top:21px;width:429px;height:260px;border-radius:12px}
.service-name{position:absolute;top:310px;width:100%;text-align:center;font-weight:700;font-size:19px}
/* contact */
.contact{position:absolute;top:2818px;left:0;width:1200px;height:543px;background:linear-gradient(135deg,#1f8a3b,var(--green) 50%,#2a9a48)}
.contact-title{width:1200px;text-align:center;top:80px;font-size:34px;color:var(--white)}
.field{position:absolute;background:var(--white);border-radius:4px;font-size:14px;color:#777;padding:16px 17px}
.submit{position:absolute;left:531px;top:392px;width:137px;height:51px;border-radius:26px;background:var(--blue);color:var(--white);font-weight:700;font-size:17px;display:flex;align-items:center;justify-content:center}
/* footer */
.footer-brand{left:106px;top:3460px;width:211px;text-align:center}
.footer-brand .brand-dot{width:80px;height:80px;margin:0 auto 8px}
.footer-brand .brand-name{font-size:19px}
.footer-brand .brand-name small{font-size:14px;letter-spacing:4px}
.social{position:absolute;top:3610px;width:25px;height:25px;border-radius:50%;background:#e01b22}
.footer-head{font-family:var(--serif);font-size:21px;color:var(--ink)}
.quick-links{left:351px;top:3455px}
.quick-links ul{list-style:none;margin-top:12px}
.quick-links li{font-size:15px;line-height:31px;display:flex;align-items:center;gap:10px}
.contact-item{position:absolute;left:519px;display:flex;align-items:center;gap:14px;font-family:var(--serif);font-size:15px}
.contact-icon{width:36px;height:36px;border-radius:50%;background:var(--blue);display:flex;align-items:center;justify-content:center}
.newsletter{left:817px;top:3455px;width:280px}
.newsletter p{font-size:15px;line-height:31px;margin-top:14px}
.email-line{position:absolute;left:820px;top:3578px;width:270px;height:26px;border-bottom:2px solid #333;font-size:14px;color:#999;padding-left:2px}
.subscribe{position:absolute;left:824px;top:3633px;width:146px;height:50px;border-radius:25px;background:var(--blue);color:var(--white);font-family:var(--serif);font-size:18px;display:flex;align-items:center;justify-content:center}
.divider{position:absolute;left:106px;top:3742px;width:986px;height:1px;background:#333}
.copyright{position:absolute;top:3762px;width:1200px;text-align:center;font-family:var(--serif);font-size:15px}
</style>
</head>
<body>

<header class="site-header">
  <div class="brand-badge">
    <div class="brand-dot"></div>
    <div class="brand-name">CORINNE HABBARD<small>CONSULTING</small></div>
  </div>
  <nav class="nav">
    <a class="active" style="left:592px">Home</a>
    <a style="left:683px">About Us</a>
    <a style="left:801px">Insights Services</a>
  </nav>
  <div class="btn" style="left:960px;top:19px;width:132px;height:47px">Contact Us</div>
</header>

<section class="hero">
  <div class="hero-photo" role="img" aria-label="Consultant smiling across a desk during a meeting with a client"></div>
  <div class="abs hero-welcome">WELCOME TO</div>
  <h1 class="abs hero-title">CORINNE HABBARD<br>CONSULTING</h1>
  <div class="btn" style="left:105px;top:354px;width:132px;height:45px">Contact Us</div>
</section>

<section class="about">
  <h2 class="abs section-title about-title">About Us</h2>
  <div class="abs about-text">
    <p>Lakeview Medicine nurse Corinne Habbard in the Civic Hall as part of the National Leadership Fellows program. The longtime member of the health system earned the honor this year and makes visits to the capital for her classes. Photo provided by Habbard.Corinne Habbard MAPLE GROVE, OR - Many Lakeview Medicine nurses have mentored Corinne Habbard throughout her 25-year career at the Maple Grove health system.</p>
    <p>The longtime nurse and current clinical information analyst now has four “mentors” in U.S. Presidents Harold Vance, Walter Reyes, Thomas Kell and Edwin Moore.</p>
  </div>
  <div class="btn" style="left:105px;top:1201px;width:132px;height:47px">Contact Us</div>
  <svg class="abs" style="left:620px;top:780px" width="480" height="480" viewBox="0 0 480 480">
    <circle cx="242" cy="240" r="231" fill="#000"/>
    <circle cx="228" cy="240" r="220" fill="#fff"/>
  </svg>
  <div class="portrait" role="img" aria-label="Portrait of the consultant"></div>
</section>

<section class="insights">
  <h2 class="abs section-title insights-title">Insights</h2>
  <div class="book" style="left:106px" role="img" aria-label="Publication cover"><div class="brand-dot"></div><span class="brand-name">CORINNE HABBARD<small>CONSULTING</small></span></div>
  <div class="book" style="left:470px" role="img" aria-label="Publication cover"><div class="brand-dot"></div><span class="brand-name">CORINNE HABBARD<small>CONSULTING</small></span></div>
  <div class="book" style="left:834px" role="img" aria-label="Publication cover"><div class="brand-dot"></div><span class="brand-name">CORINNE HABBARD<small>CONSULTING</small></span></div>
  <div class="book-caption" style="left:84px">Lorem ipsum dolor sit amet,<br>consectetur adipiscing elit</div>
  <div class="book-caption" style="left:449px">Lorem ipsum dolor sit amet,<br>consectetur adipiscing elit</div>
  <div class="book-caption" style="left:812px">Lorem ipsum dolor sit amet,<br>consectetur adipiscing elit</div>
</section>

<section class="services">
  <h2 class="abs section-title services-title">Our Services</h2>
  <p class="abs services-intro">Lorem ipsum dolor sit amet, consectetur adipiscing elit, sed do eiusmod tempor incididunt ut labore et dolore magna aliqua. Ut enim ad minim veniam, quis nostrud exercitation ullamco laboris nisi ut aliquip ex ea commodo consequat.</p>
  <div class="service-card" style="left:116px">
    <div class="service-img" role="img" aria-label="Team meeting around a table in an office" style="background:linear-gradient(90deg,#2a2a2a,#5f5a55 30%,#8b857e 50%,#4a4642 75%,#2c2c2c)"></div>
    <div class="service-name">Consulting Firm</div>
  </div>
  <div class="service-card" style="left:613px">
    <div class="service-img" role="img" aria-label="Nurse taking notes with a patient on a sofa" style="background:linear-gradient(90deg,#e8e2d8,#3c4f7a 30%,#d9d1c4 55%,#7f9fd6 80%,#ebe6de)"></div>
    <div class="service-name">Mindset and training of registered nurses</div>
  </div>
</section>

<section class="contact">
  <h2 class="abs section-title contact-title" style="color:var(--white)">Contact Us</h2>
  <div class="field" style="left:181px;top:158px;width:412px;height:50px">Name</div>
  <div class="field" style="left:606px;top:158px;width:411px;height:50px">Email</div>
  <div class="field" style="left:181px;top:221px;width:412px;height:49px">Phone Number</div>
  <div class="field" style="left:606px;top:221px;width:411px;height:49px">Subject</div>
  <div class="field" style="left:181px;top:283px;width:836px;height:86px">Message</div>
  <div class="submit">Submit</div>
</section>

<footer>
  <div class="abs footer-brand">
    <div class="brand-dot"></div>
    <div class="brand-name">CORINNE HABBARD<small>CONSULTING</small></div>
  </div>
  <div class="social" style="left:140px" role="img" aria-label="Social profile"></div>
  <div class="social" style="left:179px" role="img" aria-label="Social profile"></div>
  <div class="social" style="left:217px" role="img" aria-label="Social profile"></div>
  <div class="social" style="left:255px" role="img" aria-label="Social profile"></div>

  <div class="abs quick-links">
    <div class="footer-head" style="font-family:var(--sans);font-weight:700">Quick Links</div>
    <ul>
      <li><svg width="13" height="12" viewBox="0 0 13 12"><path d="M0 6h10M6 1l5 5-5 5" stroke="#000" stroke-width="2.2" fill="none"/></svg>Home</li>
      <li><svg width="13" height="12" viewBox="0 0 13 12"><path d="M0 6h10M6 1l5 5-5 5" stroke="#000" stroke-width="2.2" fill="none"/></svg>About Us</li>
      <li><svg width="13" height="12" viewBox="0 0 13 12"><path d="M0 6h10M6 1l5 5-5 5" stroke="#000" stroke-width="2.2" fill="none"/></svg>Insights</li>
      <li><svg width="13" height="12" viewBox="0 0 13 12"><path d="M0 6h10M6 1l5 5-5 5" stroke="#000" stroke-width="2.2" fill="none"/></svg>Services</li>
      <li><svg width="13" height="12" viewBox="0 0 13 12"><path d="M0 6h10M6 1l5 5-5 5" stroke="#000" stroke-width="2.2" fill="none"/></svg>Contact Us</li>
    </ul>
  </div>

  <div class="abs footer-head" style="left:519px;top:3455px">Contact Us</div>
  <div class="contact-item" style="top:3500px">
    <span class="contact-icon"><svg width="14" height="18" viewBox="0 0 14 18"><path d="M7 0a7 7 0 0 0-7 7c0 5 7 11 7 11s7-6 7-11a7 7 0 0 0-7-7z" fill="#fff"/><circle cx="7" cy="7" r="2.5" fill="#2a8fd1"/></svg></span>Company Name,United State.
  </div>
  <div class="contact-item" style="top:3561px">
    <span class="contact-icon"><svg width="16" height="12" viewBox="0 0 16 12"><rect width="16" height="12" rx="1.5" fill="#fff"/><path d="M1 1l7 5 7-5" stroke="#2a8fd1" stroke-width="1.5" fill="none"/></svg></span>info@compancyname.in
  </div>
  <div class="contact-item" style="top:3621px">
    <span class="contact-icon"><svg width="16" height="16" viewBox="0 0 16 16"><path d="M3 1l3 3-2 2c1 2 3 4 5 5l2-2 3 3-2 3C7 15 1 9 1 3z" fill="#fff"/></svg></span>+1888 8888 8888
  </div>

  <div class="abs newsletter">
    <div class="footer-head">Sign Up Our Newsletter</div>
    <p>Lorem ipsum dolor sit amet,consectetur adipiscing elit,adipiscing elit.</p>
  </div>
  <div class="email-line">Email</div>
  <div class="subscribe">Subscribe</div>

  <div class="divider"></div>
  <div class="copyright">Copyrights@2024.Corinne Habbard.All Rights Reserved</div>
</footer>

</body>
</html>
```